Marlow's Tide Kitchen

Marlow’s Tide Kitchen

This project is a design of a restaurant referral card used for tourist and business travelers. It needs to be 2 sided, 4/1 front color, grayscale back. I am including the specs ie, the size of the card as well as a sample card. I am also including the some pics and text. I would like a few looks for this card.

I need a card with front and back with the following specs:

• Card size 4 inch height x 2 1/8 inch width
• Top: ¾ inch Logo/header on front of card
• Front: four color
• Back: Grayscale/ black and white
* FULL Bleed for print
***Note the logo needs to be at the top 3/4 inch on the front of the card***
Front of Card:
~Logo/Restaurant name “Marlow’s Tide Kitchen” (top ¾ inch of card front)
~Marlow’s seafood is flown in daily from New England. It is our goal to serve the freshest seafood available in the Traditional New England style.

~Family Owned and operated
~ Take Out Available
~572-918-3346
~Open 7 days a week 11AM-8:00PM
~2730 W Harbor Rd New Smyrna Beach FL

www.marlowstidekitchenqrp.example
~KIDS MENU $5.99

Back of Card:
~Logo/Restaurant name “Marlow’s Tide Kitchen”
~ Freshest seafood available in the Traditional New England style
~Specialties include: Haddock, Cod, Mahi, Flounder, Fried Oysters, Whole Belly Clams, NE Steamers, Crab Legs, Lobster Salad, & much more!!
~Map (included)
~572-918-3346
~Located on A1A

Please note you can add your own flare and verbage just need the highlighted points/text above to be the focus. Would like to highlight the Fresh Seafood aspect of this restaurant. BE CREATIVE
PS I attached a sample card of front and back for specs from another card.
Also would like to see sample of card with green background similar to green in logo
Thanks,
Gerald
Updates

Industry/Entity Type

Restaurant

Colors
9bcb3c

```html
<!DOCTYPE html>
<html lang="en">
<head>
<meta charset="utf-8">
<title>Marlow's Tide Kitchen – Referral Card</title>
<link href="https://fonts.googleapis.com/css2?family=Bree+Serif&family=Oswald:wght@600;700&display=swap" rel="stylesheet">
<style>
  :root{
    --page:#e9e6e1;
    --white:#ffffff;
    --ink:#141414;
    --gray-light:#c9c9c9;
    --band:#b5b5b5;
    --teal:#2ea9c6;
    --teal-light:#4fc2dc;
    --night:#10222c;
    --food-warm:#c9782e;
    --food-red:#b3241f;
  }
  *{box-sizing:border-box;margin:0;padding:0}
  html,body{width:1200px;height:1146px;overflow:hidden;background:var(--page)}
  body{position:relative;font-family:"Bree Serif",Georgia,serif;color:var(--ink)}

  .card{position:absolute;top:73px;width:531px;height:1000px;overflow:hidden;box-shadow:0 6px 18px rgba(0,0,0,.25)}
  .card--back{left:46px;background:var(--gray-light)}
  .card--front{left:623px;background:var(--teal)}

  .scene-photo{position:absolute;inset:0}
  .card--back .scene-photo{background:linear-gradient(180deg,#bdbdbd 0%,#a3a3a3 45%,#7e7e7e 100%)}
  .card--front .scene-photo{top:520px;background:linear-gradient(180deg,#163848 0%,var(--night) 40%,#0b1820 100%)}

  .header-panel{position:absolute;left:0;top:0;width:100%;background:var(--white)}
  .card--back .header-panel{height:215px;border-top-right-radius:32% 100%}
  .card--front .header-panel{height:400px;border-top-right-radius:32% 70%}

  .brand{position:absolute;left:28px;font-family:"Bree Serif",Georgia,serif;font-weight:400;line-height:1.02}
  .card--back .brand{top:120px;font-size:38px;color:var(--ink)}
  .card--front .brand{top:230px;font-size:52px;color:var(--teal)}
  .brand-mark{display:inline-block;width:.55em;height:.55em;background:currentColor;border-radius:50%;margin-right:10px;vertical-align:.05em}

  .tagline-band{position:absolute;left:28px;right:28px;top:228px;background:var(--band);padding:10px 14px;text-align:center;font-size:25px;line-height:1.15}

  .specialties{position:absolute;left:28px;right:28px;top:335px}
  .specialties-title{background:var(--ink);color:var(--white);text-align:center;font-size:29px;font-weight:400;padding:6px 0}
  .specialties-list{background:var(--white);text-align:center;font-size:24px;line-height:1.22;padding:10px 12px 14px}

  .map-area{position:absolute;left:28px;right:28px;top:560px;height:255px;background:linear-gradient(135deg,#f2f2f2,#d6d6d6);border:3px solid var(--ink)}

  .address-box{position:absolute;background:var(--white);font-family:"Oswald","Arial Narrow",sans-serif;font-weight:700;text-align:center;color:var(--ink)}
  .card--back .address-box{left:20px;right:0;top:835px;border:3px solid var(--ink);border-right:none;font-size:27px;line-height:1.2;padding:10px 12px 10px 6px}

  .story-box{position:absolute;left:28px;right:28px;top:405px;background:var(--teal-light);color:var(--ink);text-align:center;font-size:23px;line-height:1.2;padding:14px 16px;border:3px solid var(--white)}
  .story-box strong{font-weight:400}

  .highlights{position:absolute;left:0;right:0;top:556px;text-align:center;font-family:"Oswald","Arial Narrow",sans-serif;font-weight:600;color:var(--white);font-size:27px;line-height:1.12}
  .highlights .hours{color:var(--teal-light)}
  .highlights .kids{display:inline-block;margin-top:4px;background:var(--teal);color:var(--white);padding:0 12px;font-size:24px}

  .food-photo{position:absolute;left:0;right:0;top:700px;bottom:0;background:radial-gradient(ellipse at 35% 40%,var(--food-warm) 0%,#8a4d1e 35%,var(--food-red) 65%,#3a2a22 100%)}

  .card--front .address-box{left:0;right:0;top:842px;font-size:29px;line-height:1.15;padding:8px 6px 10px}
  .address-box .web{display:block;font-family:"Bree Serif",Georgia,serif;font-weight:400;font-size:20px;line-height:1.3}
</style>
</head>
<body>

<section class="card card--back" aria-label="Card back, grayscale">
  <div class="scene-photo" role="img" aria-label="Grayscale photo of the restaurant dining room"></div>
  <div class="header-panel"></div>
  <h1 class="brand"><span class="brand-mark"></span>Marlow's<br>Tide Kitchen</h1>
  <p class="tagline-band">Freshest seafood available in the Traditional New England style</p>
  <div class="specialties">
    <h2 class="specialties-title">Specialties include:</h2>
    <p class="specialties-list">Haddock, Cod, Mahi, Flounder, Fried Oysters, Whole Belly Clams, NE Steamers, Crab Legs, Lobster Salad, &amp; much more!!</p>
  </div>
  <div class="map-area" role="img" aria-label="Street map showing the route to the restaurant on A1A"></div>
  <p class="address-box">2730 W Harbor Rd New Smyrna Beach<br>572-918-3346<br>Located on A1A</p>
</section>

<section class="card card--front" aria-label="Card front, full colour">
  <div class="scene-photo" role="img" aria-label="Dim photo of the restaurant interior"></div>
  <div class="header-panel"></div>
  <h1 class="brand"><span class="brand-mark"></span>Marlow's<br>Tide Kitchen</h1>
  <p class="story-box">Marlow’s seafood is flown in daily from New England. It is our goal to serve the freshest seafood available in the <strong>Traditional New England style.</strong></p>
  <div class="food-photo" role="img" aria-label="Photo of a fried seafood platter with steamed clams"></div>
  <p class="highlights">Family Owned and operated<br>Take Out Available<br><span class="hours">Open 7 days a week 11AM-8:00PM</span><br><span class="kids">KIDS MENU $5.99</span></p>
  <p class="address-box">2730 W Harbor Rd New Smyrna Beach FL<br>572-918-3346<span class="web">www.marlowstidekitchenqrp.example</span></p>
</section>

</body>
</html>
```